Brevard Trade Partners - we are Asian sourcing agents

We are sourcing agents based in the USA and we act as sourcing agents for clients in throughout the world. We focus primarily on custom sewn goods. So basically companies who do not have the in-house expertise to do it themselves, come to us and have us find suitable factories in Asia to do the production. We are middlemen. We find the factories...quote the project...manage the quality control and then deliver the goods directly to our customer's door. We pride ourselves in making the communication very easy and precise.

Current page is www.brevardtradepartners.com

I am not happy w/ the overall look. The spacing...the photos, the fonts...the design elements...the pictures. I want a cool, crisp design that conveys professionalism and clearly depicts/explains what we do.

Requirements
Must have
• use my logo....I like it...it was designed by someone on this website.
Nice to have
• a video/animation of the entire process would be wonderful. Showing initial contact with our office in the USA...then to my correspondence with my offices in Taiwan and in Hong Kong...and then back and fort w/ the customer.....and then between my people in Hong Kong/Taiwan with the local factories......and then a quote is generated and sent to my client......to samples being made and sent for approval.....to a PO being generated......to final samples being sent.....to the order being shipped and delivered to the clients warehouse. I was thinking of an animation showing arrows and text showing the back and forth communication and explaining how the process flows.

```html
<!DOCTYPE html>
<html lang="en">
<head>
<meta charset="utf-8">
<title>Brevard Trade Partners – Asian Outsourcing Made Easy</title>
<link rel="stylesheet" href="https://fonts.googleapis.com/css2?family=Roboto:wght@300;400;500;700&family=Oswald:wght@500;600&display=swap">
<style>
:root{
  --green:#5f8f12;
  --green-dark:#4d7a0b;
  --green-light:#6f9e1c;
  --green-bright:#78a81e;
  --navy:#1b2a6b;
  --navy-deep:#14205a;
  --grey-band:#efefef;
  --text:#555;
  --white:#fff;
  --footer-bottom:#4a6e12;
}
*{margin:0;padding:0;box-sizing:border-box}
html,body{width:1200px;height:2791px;overflow:hidden}
body{position:relative;background:var(--white);font-family:"Roboto",Arial,sans-serif;color:var(--text)}
.abs{position:absolute}
.top-rule{left:0;top:0;width:1200px;height:5px;background:var(--green)}

/* header */
.brand{left:75px;top:30px;display:flex;align-items:center;gap:12px}
.brand-mark{width:18px;height:18px;background:var(--green)}
.brand-name{font-family:"Roboto",sans-serif;font-weight:700;font-size:26px;color:var(--navy);letter-spacing:.5px}
.header-contact{right:75px;top:30px;font-size:16px;color:var(--navy)}
.header-contact div{display:flex;align-items:center;gap:12px;height:28px}
.header-contact a{color:var(--green);text-decoration:none}
.ico{width:18px;height:18px;background:var(--navy);border-radius:2px;display:flex;align-items:center;justify-content:center}

/* nav */
.main-nav{left:74px;top:97px;width:1052px;height:52px;background:var(--green);display:flex;align-items:center}
.main-nav ul{list-style:none;display:flex;gap:0;padding-left:24px;flex:1}
.main-nav li{color:var(--white);font-size:15px;margin-right:49px}
.nav-quote{width:280px;height:52px;background:var(--navy);display:flex;align-items:center;color:var(--white);font-size:20px;font-weight:500}
.nav-quote svg{margin-right:24px}

/* hero */
.hero{left:74px;top:160px;width:1052px;height:389px;border:3px solid #d9d9d9}
.hero-photo{position:absolute;inset:0;background:linear-gradient(90deg,#bfe0b8 0%,#a9d5a4 45%,#8fb18c 70%,#5b6d62 100%)}
.hero-title{left:34px;top:82px;font-family:"Oswald",sans-serif;font-weight:600;font-size:46px;color:var(--navy-deep);letter-spacing:-.5px}
.hero-sub{left:34px;top:142px;font-size:30px;line-height:40px;color:#2b2f2b;font-weight:400}
.btn-green{left:34px;top:250px;width:220px;height:48px;background:var(--green);color:var(--white);font-size:19px;display:flex;align-items:center;justify-content:center;border-bottom:3px solid var(--green-dark)}
.dots{left:34px;top:348px;display:flex;gap:8px}
.dots span{width:10px;height:10px;border-radius:50%;background:#2a3a4a}

/* welcome */
.center{left:0;width:1200px;text-align:center}
.welcome-title{top:584px;font-size:26px;color:var(--navy)}
.welcome-sub{top:632px;font-size:18px;font-weight:500;color:var(--green)}
.welcome-copy{left:110px;top:667px;width:980px;text-align:center;font-size:12.5px;line-height:22px}

.band{left:0;width:1200px;background:var(--grey-band);display:flex;align-items:center;justify-content:center;font-size:26px;color:var(--navy)}
.band-products{top:768px;height:54px}
.band-how{top:1382px;height:56px}

/* product cards */
.card{background:var(--green);border:2px solid var(--green-dark)}
.card .photo{position:absolute;left:16px;top:16px;right:16px;background:#fff}
.card .label{position:absolute;left:0;right:0;bottom:14px;text-align:center;color:var(--white);font-size:19px}

/* video */
.video{left:255px;top:1464px;width:690px;height:322px;border:3px solid #ccc;background:linear-gradient(135deg,#3c3c3c,#1f1f1f 60%,#2e2e2e)}
.video svg{position:absolute;left:50%;top:50%;transform:translate(-50%,-50%)}

/* cta */
.cta{left:0;top:1817px;width:1200px;height:201px;background:var(--green-light)}
.cta-title{top:1848px;font-size:26px;color:var(--white)}
.cta-sub{top:1890px;font-size:14px;color:var(--white)}
.btn-navy{left:491px;top:1934px;width:220px;height:47px;background:var(--navy);color:var(--white);font-size:19px;display:flex;align-items:center;justify-content:center;border-bottom:3px solid #0e1640}

/* about */
.about{left:74px;top:2046px;width:679px}
.about h2{font-size:26px;font-weight:400;color:var(--navy)}
.about h3{font-size:18px;font-weight:500;color:var(--green);margin-top:16px}
.about p{font-size:12.6px;line-height:22.5px;margin-top:6px}
.divider{left:787px;top:2050px;width:1px;height:218px;background:#d5d5d5}
.know{left:817px;top:2046px;width:320px}
.know h2{font-size:26px;font-weight:400;color:var(--navy)}
.know ul{list-style:none;margin-top:12px}
.know li{font-size:13px;height:32px;display:flex;align-items:center;gap:10px}

/* footer */
.site-footer{left:0;top:2306px;width:1200px;height:428px;background:var(--green-bright)}
.fcol{top:2342px}
.fcol h4{font-size:14px;font-weight:400;color:var(--navy);text-transform:uppercase;margin-bottom:8px}
.fcol ul{list-style:none}
.fcol li{font-size:12px;color:var(--white);height:26px;line-height:26px}
.fcol h4.next{margin-top:18px}
.contact-info p{font-size:12px;color:var(--white);line-height:20px}
.contact-info .co{color:var(--navy);font-weight:500;font-size:12px}
.contact-info .link{color:var(--navy)}
.social{display:flex;gap:8px;margin-top:12px}
.social span{width:28px;height:28px;border-radius:50%;background:var(--white)}
.copyright{left:0;top:2734px;width:1200px;height:57px;background:var(--footer-bottom);display:flex;align-items:center;justify-content:center;color:#d8e6c2;font-size:12px}
</style>
</head>
<body>
<div class="abs top-rule"></div>

<header>
  <div class="abs brand"><span class="brand-mark"></span><span class="brand-name">BREVARD TRADE PARTNERS</span></div>
  <div class="abs header-contact">
    <div><span class="ico"><svg width="12" height="12" viewBox="0 0 12 12"><path d="M2 1l2 0 1 3-1.5 1a7 7 0 0 0 3.5 3.5L8 7l3 1v2c0 .6-.4 1-1 1A9 9 0 0 1 1 2c0-.6.4-1 1-1z" fill="#fff"/></svg></span>Tel: 555-014-2290</div>
    <div><span class="ico"><svg width="12" height="10" viewBox="0 0 12 10"><rect x=".5" y=".5" width="11" height="9" fill="none" stroke="#fff"/><path d="M.5 .5l5.5 5 5.5-5" fill="none" stroke="#fff"/></svg></span>Email: <a>info@brevardtradepartners.com</a></div>
  </div>
  <nav class="abs main-nav">
    <ul><li>HOME</li><li>ABOUT US</li><li>PRODUCT CATEGORIES</li><li>NEWS</li><li>FAQ</li><li>CONTACT US</li></ul>
    <div class="nav-quote"><svg width="60" height="52" viewBox="0 0 60 52"><path d="M0 0h14l26 26-26 26H0l26-26z" fill="#fff"/><path d="M14 14h8l12 12-12 12h-8l12-12z" fill="#1b2a6b"/></svg>REQUEST A QUOTE</div>
  </nav>
</header>

<section class="abs hero">
  <div class="hero-photo" role="img" aria-label="Worker operating an industrial sewing machine on red fabric in a factory"></div>
  <h1 class="abs hero-title">Asian Outsourcing Made Easy!</h1>
  <p class="abs hero-sub">Custom Sewn Goods Made to<br>Your Specifications..</p>
  <div class="abs btn-green">REQUEST A QUOTE</div>
  <div class="abs dots"><span></span><span></span><span></span><span></span></div>
</section>

<h2 class="abs center welcome-title" style="font-weight:400">Welcome to Our Website</h2>
<h3 class="abs center welcome-sub">Sourcing Custom Goods in China</h3>
<p class="abs welcome-copy">We outsource sewing services direct from China. Our long-established and extensive network of offshore factory-partners provides our clients with access to a wide variety of contract sewing expertise from Chinese manufacturers. Clients only need to communicate with our US agents, but will have the benefits of the cost savings &amp; quality workmanship from offshore outsourcing from Asia.</p>

<div class="abs band band-products">Product Categories</div>

<div class="abs card" style="left:74px;top:850px;width:331px;height:238px"><div class="photo" style="height:170px;background:linear-gradient(135deg,#7a6a66,#c53a2c 60%,#e0d6d0)" role="img" aria-label="Hands guiding red fabric through a sewing machine"></div><div class="label">Sewn Goods</div></div>
<div class="abs card" style="left:435px;top:850px;width:330px;height:238px"><div class="photo" style="height:170px;background:radial-gradient(ellipse at center,#3a3a3a 0%,#555 35%,#fff 70%)" role="img" aria-label="Black and red messenger bag"></div><div class="label">Bags</div></div>
<div class="abs card" style="left:794px;top:850px;width:332px;height:238px"><div class="photo" style="height:170px;background:radial-gradient(ellipse at center,#666 0%,#bbb 40%,#fff 72%)" role="img" aria-label="Pair of black and grey ski gloves"></div><div class="label">Gloves</div></div>

<div class="abs card" style="left:74px;top:1110px;width:242px;height:239px"><div class="photo" style="height:170px;background:radial-gradient(ellipse at center,#2b3a8a 0%,#3c4a9a 40%,#fff 72%)" role="img" aria-label="Motorcycle under a navy protective cover"></div><div class="label">Covers</div></div>
<div class="abs card" style="left:344px;top:1110px;width:242px;height:239px"><div class="photo" style="height:170px;background:linear-gradient(90deg,#fff 8%,#2a2a6a 15%,#7a2aa0 30%,#d02a7a 45%,#c0241e 60%,#333 75%,#fff 85%)" role="img" aria-label="Row of colourful phone cases"></div><div class="label">Cases</div></div>
<div class="abs card" style="left:614px;top:1110px;width:242px;height:239px"><div class="photo" style="height:170px;background:radial-gradient(ellipse at center,#c9d8ee 0%,#e6edf7 40%,#fff 70%)" role="img" aria-label="Quilted medical pad"></div><div class="label">Medical</div></div>
<div class="abs card" style="left:884px;top:1110px;width:242px;height:239px"><div class="photo" style="height:170px;background:radial-gradient(ellipse at center,#b82a2a 0%,#333 40%,#fff 72%)" role="img" aria-label="Group of red, black and white golf bags"></div><div class="label">Sporting Goods</div></div>

<div class="abs band band-how">How it Works</div>
<div class="abs video" role="img" aria-label="Video still of workers at sewing stations in a factory">
  <svg width="110" height="110" viewBox="0 0 110 110"><circle cx="55" cy="55" r="50" fill="rgba(0,0,0,.25)" stroke="#fff" stroke-width="5"/><path d="M42 32l34 23-34 23z" fill="#fff"/></svg>
</div>

<section class="abs cta"></section>
<h2 class="abs center cta-title" style="font-weight:400">Outsource Your Sewing Needs to Trusted Contractors in China</h2>
<p class="abs center cta-sub">Please contact us for immediate consultation regarding your outsourcing project.</p>
<div class="abs btn-navy">REQUEST A QUOTE</div>

<section class="abs about">
  <h2>About Our Company</h2>
  <h3>Don't go at it alone!</h3>
  <p>Brevard Trade Partners has been sourcing custom sewn goods in Asia since 1998. We work with our clients by matching their unique production needs with the best possible China sewing factories. We manage the entire process from start to finish, by first identifying the best factories to quote each job. The next step is negotiating the best (fair) price possible. We complete the process by monitoring the quality of the goods during production, and then managing the ocean logistics, customs clearances and local delivery right to your door. Our services and our total commitment to customer satisfaction help level the playing field by giving our customers access to low cost, high quality China contract sewing.</p>
</section>
<div class="abs divider"></div>
<section class="abs know">
  <h2>What You Need to Know</h2>
  <ul>
    <li><svg width="12" height="10" viewBox="0 0 12 10"><path d="M1 5l3.5 3.5L11 1" fill="none" stroke="#5f8f12" stroke-width="2.2"/></svg>Contract Sewing in China</li>
    <li><svg width="12" height="10" viewBox="0 0 12 10"><path d="M1 5l3.5 3.5L11 1" fill="none" stroke="#5f8f12" stroke-width="2.2"/></svg>What is the Process?</li>
    <li><svg width="12" height="10" viewBox="0 0 12 10"><path d="M1 5l3.5 3.5L11 1" fill="none" stroke="#5f8f12" stroke-width="2.2"/></svg>What the Minimum Order?</li>
    <li><svg width="12" height="10" viewBox="0 0 12 10"><path d="M1 5l3.5 3.5L11 1" fill="none" stroke="#5f8f12" stroke-width="2.2"/></svg>Contract Outsourcing FAQ</li>
    <li><svg width="12" height="10" viewBox="0 0 12 10"><path d="M1 5l3.5 3.5L11 1" fill="none" stroke="#5f8f12" stroke-width="2.2"/></svg>Outsourcing Case Study</li>
    <li><svg width="12" height="10" viewBox="0 0 12 10"><path d="M1 5l3.5 3.5L11 1" fill="none" stroke="#5f8f12" stroke-width="2.2"/></svg>Custom Industrial Sewing in China</li>
  </ul>
</section>

<footer>
  <div class="abs site-footer"></div>
  <div class="abs fcol" style="left:74px"><h4>Custom Bags</h4><ul><li>Athletic Bags</li><li>Backpacks</li><li>Computer Bags</li><li>Cooler Bags</li><li>Cosmetic Bags</li><li>Handbags</li><li>Messenger Bags</li><li>Shopping Bags</li><li>Tool Bags</li><li>Travel Bags</li><li>Yoga Bags</li></ul></div>
  <div class="abs fcol" style="left:238px"><h4>Custom Covers</h4><ul><li>ATV Covers</li><li>Chair Covers</li><li>Equipment Covers</li><li>Golf Cart Covers</li><li>Motorcycle Covers</li><li>Outdoor Furniture Covers</li><li>Outdoor Grill Cover</li><li>Personal Watercraft Covers</li><li>Snowmobile Covers</li></ul><h4 class="next">Custom Sewn Goods</h4><ul><li>Pet Collars, Leashes, &amp; Harnesses</li><li>Socks</li></ul></div>
  <div class="abs fcol" style="left:459px"><h4>Custom Medical Accessories</h4><ul><li>Medical Equipment Covers</li><li>Medical Pads</li><li>Medical Sheets &amp; Bedding Supplies</li><li>Oxygen Tank Cases and Bags</li></ul><h4 class="next">Custom Cases</h4><ul><li>Cosmetic Cases</li><li>Phone Cases</li><li>Tool Bags and Tool Cases</li></ul><h4 class="next">Custom Sporting Goods</h4><ul><li>Yoga Mats</li><li>Yoga Gear and Accessories</li></ul></div>
  <div class="abs fcol" style="left:733px"><h4>Custom Gloves</h4><ul><li>Batting Gloves</li><li>Garden Gloves</li><li>Mechanic Gloves</li><li>Safety Gloves</li><li>Ski Gloves</li></ul><h4 class="next">Custom Gloves</h4><ul><li>Batting Gloves</li><li>Garden Gloves</li><li>Mechanic Gloves</li><li>Safety Gloves</li><li>Ski Gloves</li></ul></div>
  <div class="abs fcol contact-info" style="left:915px"><h4>Contact Info</h4>
    <p class="co">BREVARD TRADE PARTNERS, LLC</p>
    <p>48 Harbor Lane<br>Suite B-2<br>Melbourne, FL 32901</p>
    <p class="link" style="margin-top:6px">Online: Inquiry Form</p>
    <p>Tel: 555-014-2290<br>Fax: 555-014-2291<br>Email: info@brevardtradepartners.com</p>
    <h4 style="margin-top:22px">Connect Us</h4>
    <div class="social"><span></span><span></span><span></span><span></span><span></span></div>
  </div>
  <div class="abs copyright">Copyright © 2015 Brevard Trade Partners, LLC. | USA - Hong Kong - Taipei All Right Reserved</div>
</footer>
</body>
</html>
```